Anzeigengestaltung für Reinigungsunternehmen
Zielgruppe
Wir sind ein Reinigungsunternehmen mit den Haupttätigkeitsfeldern: Büroreinigung, Treppenhausreinigung und Bauendreinigung.
Webseite: www.kolbrapflege.de
Die Zielgruppe sind Unternehmer (überwiegend Büros), Hausverwaltungen sowie Bauherren.
Aufgabenstellung
Die Reinigungsfirma wird mit dieser Anzeige zum ersten Mal beworben.
Umkreis: Kreis Paderborn und Kreis Gütersloh
Die Anzeige soll sowohl in Facebook beworben werden, sowie auch in den örtlichen Rundschauen.

```html
<!DOCTYPE html>
<html lang="de">
<head>
<meta charset="utf-8">
<title>Kolbra Pflege – Anzeige</title>
<link rel="stylesheet" href="https://fonts.googleapis.com/css2?family=Montserrat:ital,wght@0,400;0,500;0,700;1,400;1,600&display=swap">
<style>
  :root {
    --navy: #0f4f7a;
    --royal: #1f3fd6;
    --teal: #3dbdaf;
    --teal-dark: #2fa597;
    --white: #ffffff;
    --panel: rgba(255,255,255,0.82);
    --strip: #f3f4f5;
  }
  * { margin: 0; padding: 0; box-sizing: border-box; }
  html, body { width: 810px; height: 1200px; overflow: hidden; background: var(--white); }
  .ad {
    position: relative; width: 810px; height: 1200px; overflow: hidden;
    font-family: "Montserrat", Arial, sans-serif;
  }
  .ad__photo {
    position: absolute; inset: 0;
    background:
      radial-gradient(ellipse 260px 520px at 740px 620px, rgba(240,228,150,0.85), rgba(240,228,150,0) 70%),
      radial-gradient(ellipse 220px 380px at 150px 420px, rgba(150,170,190,0.55), rgba(150,170,190,0) 70%),
      linear-gradient(180deg, #dfe6ec 0%, #eef1f4 40%, #e6eaee 100%);
  }
  .ad__panel {
    position: absolute; left: 0; top: 279px; width: 810px; height: 800px;
    background: var(--panel);
    border-top-right-radius: 130px;
  }
  .brand {
    position: absolute; top: 350px; left: 0; width: 810px;
    display: flex; justify-content: center; align-items: center; gap: 18px;
  }
  .brand__mark { width: 54px; height: 54px; background: var(--teal); }
  .brand__text { display: flex; flex-direction: column; }
  .brand__name { font-size: 44px; font-weight: 700; color: var(--royal); line-height: 1; }
  .brand__owner { font-size: 16px; font-weight: 400; color: var(--teal-dark); margin-top: 8px; }
  .headline {
    position: absolute; top: 528px; left: 0; width: 810px; text-align: center;
    font-size: 49px; font-weight: 700; color: var(--navy); line-height: 63px; letter-spacing: 0.5px;
  }
  .subline {
    position: absolute; top: 688px; left: 0; width: 810px; text-align: center;
    font-size: 29px; font-style: italic; font-weight: 400; color: var(--navy); line-height: 43px;
  }
  .services {
    position: absolute; top: 810px; left: 224px; list-style: none;
  }
  .services li {
    display: flex; align-items: center; height: 59px;
    font-size: 33px; font-weight: 400; color: var(--navy); letter-spacing: 0.3px;
  }
  .services svg { width: 36px; height: 30px; margin-right: 20px; flex: none; }
  .footer {
    position: absolute; left: 0; top: 1078px; width: 810px; height: 95px;
    background: var(--teal); color: var(--white);
    font-size: 17px; text-align: center; padding-top: 21px; line-height: 31px;
  }
  .footer__row { display: flex; justify-content: center; align-items: center; gap: 8px; }
  .footer__sep { margin: 0 6px; }
  .footer svg { width: 16px; height: 14px; }
  .footer__gap { width: 16px; }
  .strip { position: absolute; left: 0; top: 1173px; width: 810px; height: 27px; background: var(--strip); }
</style>
</head>
<body>
<main class="ad">
  <div class="ad__photo" role="img" aria-label="Foto: Reinigungskraft wischt den Boden, im Vordergrund gelbe Handschuhe und Eimer"></div>
  <div class="ad__panel"></div>

  <div class="brand">
    <div class="brand__mark"></div>
    <div class="brand__text">
      <span class="brand__name">Kolbra Pflege</span>
      <span class="brand__owner">Inh. Marten Voss</span>
    </div>
  </div>

  <h1 class="headline">SCHENKEN SIE IHREM<br>OBJEKT NEUEN GLANZ</h1>
  <p class="subline">Zuverlässige und professionelle<br>Reinigungskräfte in Paderborn &amp; Gütersloh</p>

  <ul class="services">
    <li><svg viewBox="0 0 36 30"><path d="M22 14 L34 3" stroke="#0f4f7a" stroke-width="3.5" stroke-linecap="round"/><path d="M3 27 Q6 16 16 11 L24 19 Q18 27 3 27 Z" fill="#0f4f7a"/></svg>Büroreinigung</li>
    <li><svg viewBox="0 0 36 30"><path d="M22 14 L34 3" stroke="#0f4f7a" stroke-width="3.5" stroke-linecap="round"/><path d="M3 27 Q6 16 16 11 L24 19 Q18 27 3 27 Z" fill="#0f4f7a"/></svg>Treppenhausreinigung</li>
    <li><svg viewBox="0 0 36 30"><path d="M22 14 L34 3" stroke="#0f4f7a" stroke-width="3.5" stroke-linecap="round"/><path d="M3 27 Q6 16 16 11 L24 19 Q18 27 3 27 Z" fill="#0f4f7a"/></svg>Bauendreinigung</li>
    <li><svg viewBox="0 0 36 30"><path d="M22 14 L34 3" stroke="#0f4f7a" stroke-width="3.5" stroke-linecap="round"/><path d="M3 27 Q6 16 16 11 L24 19 Q18 27 3 27 Z" fill="#0f4f7a"/></svg>Lorem ipsum</li>
  </ul>

  <footer class="footer">
    <div class="footer__row">Lindenweg 12<span class="footer__sep">•</span>33100 Talbrück</div>
    <div class="footer__row">
      <svg viewBox="0 0 16 14"><rect x="1" y="2" width="14" height="10" rx="1.5" fill="none" stroke="#fff" stroke-width="1.6"/><path d="M1.5 3 L8 8 L14.5 3" fill="none" stroke="#fff" stroke-width="1.6"/></svg>
      <span>info@kolbrapflege.de</span>
      <span class="footer__gap"></span>
      <svg viewBox="0 0 16 14"><rect x="3" y="2" width="10" height="7.5" rx="1" fill="none" stroke="#fff" stroke-width="1.6"/><path d="M1 11.5 H15" stroke="#fff" stroke-width="1.8" stroke-linecap="round"/></svg>
      <span>www.kolbrapflege.de</span>
    </div>
  </footer>
  <div class="strip"></div>
</main>
</body>
</html>
```